brovlanepass.net

Develop a website for brolanepass.net will be a site to sell tickets for concerts, shows, shows, theaters and others. I need a web design easy view, very easy to use and accumulate events by date. The aim is to develop the site was connected to a complex system that is already developed. (Important this page to a robust system was connected via links the idea is to develop only the front view)
Updates

Reason: I need more designs yet we have not made the decision

Target Market(s)

millennials, adults, who want to enjoy concerts and shows

Industry/Entity Type

Event

Number of Pages Required

5+ page

Colors
1b1b1b
aaaaaa
ffffff

Requirements
Must have
• Easy Vista, accumulation of upcoming events, past events. The tabs should have are: 1 Start: In this part of upcoming events occur. You could put a banner on the top and down the events by date. 2. How to order: page with instructions on how to purchase tickets 3. About Us: The company history 4. Contact: Phones and template for contact by mail 5. Our policies: shopping 6. Notice Privacy: Privacy Notice Copoy 7. Centers Sale: physical places where they can purchase tickets Promoters 8. access: Link to a template
Nice to have
• as you can see p www.quimbarostage.net or farunda.net or farunda.org or gallowmerk.net (important this page to a robust system was connected via links the idea is to develop only the front view)
Should not have
• Many things Tangled

```html
<!DOCTYPE html>
<html lang="es">
<head>
<meta charset="utf-8">
<title>brolanepass.net – Aviso de Privacidad</title>
<link href="https://fonts.googleapis.com/css2?family=Questrial&display=swap" rel="stylesheet">
<style>
:root{
  --page-bg-light:#f2f2f2;
  --page-bg-dark:#b9b9b9;
  --white:#ffffff;
  --nav:#1b1b1b;
  --frame:#c9c9c9;
  --body:#1d272b;
  --panel:#1a2326;
  --text:#f2f2f2;
  --muted:#aaaaaa;
  --menu:#d8d8d8;
}
*{margin:0;padding:0;box-sizing:border-box}
html,body{width:1200px;height:1000px;overflow:hidden}
body{
  position:relative;
  font-family:"Questrial",sans-serif;
  background:radial-gradient(ellipse at 50% 50%,var(--page-bg-light) 0%,var(--page-bg-dark) 100%);
}
.site{position:absolute;left:18px;top:168px;width:1174px;height:654px;background:var(--body)}
.topbar{position:absolute;left:0;top:0;width:1174px;height:37px;background:var(--white)}
.nav{position:absolute;left:224px;top:0;width:691px;height:37px;background:var(--nav)}
.nav a{position:absolute;top:9px;color:var(--menu);font-size:15px;text-decoration:none;white-space:nowrap}
.banner{position:absolute;left:0;top:37px;width:1174px;height:108px;background:var(--body)}
.frame{position:absolute;top:0;height:108px;background:var(--frame)}
.photo{position:absolute;top:0;height:108px}
.photo-band{left:19px;width:343px;background:linear-gradient(90deg,#2a2a2a,#5c5c5c 40%,#1e1e1e 75%,#4a4a4a)}
.photo-stage{left:372px;width:467px;background:radial-gradient(circle at 62% 40%,#ffb35a 0%,#d4441f 18%,#6e1412 45%,#1e0808 80%)}
.photo-valley{left:848px;width:306px;background:linear-gradient(180deg,#a9b6ae 0%,#6f8a6c 45%,#334a2e 100%)}
.submenu{position:absolute;left:490px;top:0;width:133px;height:103px;background:var(--nav)}
.submenu hr{position:absolute;left:12px;width:108px;border:0;border-top:1px solid #9a9a9a}
.submenu a{position:absolute;left:0;width:133px;text-align:center;color:var(--menu);font-size:13px;text-decoration:none}
.page-title{position:absolute;left:144px;top:158px;color:var(--white);font-size:15px;font-weight:700}
.side-photo{position:absolute;left:0;top:178px;width:85px;height:404px;background:linear-gradient(180deg,#8c9a92 0%,#526256 30%,#222 60%,#5c6f70 100%)}
.side-water{position:absolute;left:10px;top:582px;width:142px;height:50px;background:linear-gradient(180deg,#6c7c78,#c9d0cc 60%,#8c9896)}
.content{position:absolute;left:85px;top:187px;width:1089px;height:395px;background:var(--panel);padding:14px 80px 0 21px;color:var(--text);font-size:7.6px;line-height:7.4px}
.content p{margin-bottom:5.6px}
.footer-name{position:absolute;left:172px;top:604px;color:#bdbdbd;font-size:14px;font-weight:700}
</style>
</head>
<body>
<div class="site">
  <header class="topbar">
    <nav class="nav">
      <a style="left:31px">Inico</a>
      <a style="left:115px">Comprar Boleto</a>
      <a style="left:288px">Quienes Somos</a>
      <a style="left:441px">Contacto</a>
      <a style="left:563px">Mi Cuenta</a>
    </nav>
  </header>

  <section class="banner">
    <div class="frame" style="left:10px;width:9px"></div>
    <div class="photo photo-band" role="img" aria-label="Fotografía de una banda de rock con gafas de sol"></div>
    <div class="frame" style="left:362px;width:10px"></div>
    <div class="photo photo-stage" role="img" aria-label="Luces rojas y naranjas de un escenario en concierto"></div>
    <div class="frame" style="left:839px;width:9px"></div>
    <div class="photo photo-valley" role="img" aria-label="Músico de pie ante un valle verde con montañas"></div>
    <div class="frame" style="left:1154px;width:8px"></div>
    <div class="submenu">
      <hr style="top:12px">
      <a style="top:19px">Nuestras Políticas</a>
      <hr style="top:47px">
      <a style="top:57px">Aviso de Privacidad</a>
      <hr style="top:84px">
    </div>
  </section>

  <h1 class="page-title">Aviso de Privacidad</h1>
  <div class="side-photo" role="img" aria-label="Músico con guitarra pequeña junto a un río"></div>
  <div class="side-water" role="img" aria-label="Reflejos de agua del río"></div>

  <main class="content">
    <p>Este sitio es operado por Venta Quimbaro de entradas nv. Al visitar este sitio web o utilizar, usted acepta los términos de las ventas en línea y privacidad de Venta Quimbaro de entradas, como la que se expone a continuación. Si no está de acuerdo con estos términos, por favor no visitar este sitio o su uso.</p>
    <p>Este sitio web contiene enlaces a sitios de terceros. Venta Quimbaro de entradas nv no tiene control sobre estos sitios y no es responsable de su contenido, sus efectos y sus prácticas, incluso en términos de su política de privacidad.</p>
    <p>Cuando otros sitios Web contienen un vínculo a la página web de Venta Quimbaro de entradas nv, esto no quiere decir que recomendamos estos sitios o que se expresan las opiniones allí está.</p>
    <p>Todos los textos, imágenes y fotos en nuestro sitio tienen derechos de autor y no pueden ser utilizados sin el permiso previo por escrito de Venta Quimbaro de entradas nv, para cualquier propósito.</p>
    <p>Comisión para la Protección de Privacidad - sitio web</p>
    <p>Nr. QVN 2016-04718-035-RT</p>
    <p>Recopilación de información personal</p>
    <p>Cuando se realiza una acción en este sitio web (por ejemplo, entradas. Reserva) Venta Quimbaro de entradas nv le pedirá que proporcione cierta información sobre usted en línea. Venta Quimbaro de entradas nv recoge esta información para procesar su reserva y se puede fácilmente mantener al corriente de los acontecimientos.</p>
    <p>Sus datos a nuestros socios, incluyendo Dravemont Data NV (Vennelaan 12 en 1090) recibieron de manera que u otras empresas (como socios comerciales, socios del sector de la caridad, de asociaciones o grupos de interés y grupos de opinión) que personalizar las ofertas promocionales o investigación de mercado puede proporcionar, posiblemente basado en un análisis de su perfil. Si usted no desea esto, por favor escríbanos a la dirección indicada más abajo en esta página web. Su dirección de correo electrónico sólo será transferida a nuestros asociados proporcionaron su consentimiento expreso.</p>
    <p>Puede consultar el registro público para obtener información adicional (Comisión para la protección de la intimidad, la calle Veren 18, 1000 Bruselas).</p>
    <p>El uso de cookies</p>
    <p>www.quimbarostage.net Cuando se visita, se puede navegar de forma anónima en el sitio web y tener acceso a información importante sin revelar su identidad. Para mejorar nuestro sitio web, utilizamos "cookies" para rastrear su visita. Una cookie es una pequeña cantidad de datos que se envía por el servidor web a su navegador y que sólo puede ser leído por el servidor que los datos se pasan a usted. Funciona como su tarjeta de identificación, sus contraseñas, compras y preferencias se registran en ella. Una cookie no puede ser ejecutado como código o contener virus.</p>
    <p>La mayoría de los navegadores están configurados para aceptar cookies. Usted puede configurar su navegador para que le avise cuando reciba una cookie, dándole la oportunidad de decidir si acepta la cookie o no. Para visitar algunas páginas web cookies tienen que ser aceptadas. Los usuarios que deseen recibir las cookies no tendrán acceso en ese caso a este tipo de páginas web.</p>
    <p>Venta Quimbaro de entradas nv utiliza Aunque las cookies para rastrear su visita a www.quimbarostage.net y nuestros servidores web registra automáticamente la dirección de Internet / IP de su ordenador, pero esta información no le identifica personalmente y permanecer en el anonimato a menos Venta de entradas que ha proporcionado la información personal de otro modo.</p>
    <p>Actualizar su información personal</p>
    <p>Usted tiene derecho a acceder a su información personal y sus preferencias en cuanto a su privacidad. Usted también tiene el derecho de corregir dicha información o que se lo retiren. Puede hacerlo escribiendo a Venta Quimbaro de entradas nv en la siguiente dirección:</p>
    <p>Venta de entradas Quimbaro nv<br>Lindevaartweg 84<br>2180 Haverkem<br>Bélgica</p>
    <p>Por favor, incluya su nombre, dirección y / o dirección de correo electrónico cuando se comunique con nosotros.</p>
    <p>disputas</p>
    <p>Cualquier disputa que serán sometidos a la jurisdicción competente, de conformidad con el art. 624 1 º, 2 º y 4 º del Código Judicial.</p>
    <p>Cómo darse de baja?</p>
    <p>Puede darse de baja en cualquier momento haciendo clic en el enlace para darse de baja en la parte inferior de cada correo electrónico (en línea) o al permitir que a través del contacto que hay una correspondencia (sin conexión) desea recibir. A continuación, hay más correos electrónicos (excepto los correos electrónicos que tienen que ver directamente con la reserva) y recibir correo.</p>
  </main>

  <div class="footer-name">brolanepass.net</div>
</div>
</body>
</html>
```